corvale institute of business and technology web site

I need web site for the institute which focus on business courses and computer course it is also for vocation train for employment It is also carear development and advancement .It should have links to online study resource which free
Industry/Entity Type
Business
Number of Pages Required
1 page
Look and feel
Each slider illustrates characteristics of the customer's brand and the style your logo design should communicate.

```html
<!DOCTYPE html>
<html lang="en">
<head>
<meta charset="utf-8">
<title>Corvale Institute of Business and Technology</title>
<link href="https://fonts.googleapis.com/css2?family=Oswald:wght@400;500;700&family=Open+Sans:ital,wght@0,400;0,600;0,700;1,400&display=swap" rel="stylesheet">
<style>
:root{
  --blue:#1d6fbf;
  --blue-dark:#12508f;
  --navy:#0f2c52;
  --green:#7dc21e;
  --green-btn:#8cc63f;
  --ink:#333;
  --muted:#777;
  --light:#f0f0f0;
  --footer:#2a2a2a;
  --footer-deep:#1c1c1c;
  --white:#fff;
}
*{box-sizing:border-box;margin:0;padding:0}
html,body{width:1200px;height:3200px;overflow:hidden}
body{font-family:"Open Sans",Arial,sans-serif;color:var(--ink);background:var(--white);font-size:14px;line-height:1.5}

/* header */
.site-header{position:relative;height:180px;background:var(--white);border-bottom:4px solid var(--blue)}
.brand{position:absolute;left:40px;top:24px;width:330px;height:130px;display:flex;align-items:center;gap:16px}
.brand-mark{width:56px;height:56px;border-radius:50%;background:var(--blue);flex:none}
.brand-name{font-family:"Oswald",sans-serif;font-weight:700;font-size:40px;color:var(--navy);line-height:1}
.brand-sub{font-family:"Oswald",sans-serif;font-weight:700;font-size:13px;color:var(--navy);letter-spacing:.5px;margin-top:6px}
.contact-strip{position:absolute;right:40px;top:18px;display:flex;gap:36px;align-items:center;font-size:14px;color:var(--navy)}
.contact-strip small{display:block;font-size:11px;color:var(--muted);text-transform:uppercase}
.contact-item{display:flex;gap:10px;align-items:center}
.socials{display:flex;gap:8px}
.socials span{width:30px;height:30px;border-radius:50%;background:var(--navy);display:block}
.main-nav{position:absolute;left:420px;top:110px;display:flex;gap:40px;font-family:"Oswald",sans-serif;font-size:18px;color:var(--navy);letter-spacing:.5px}
.search{position:absolute;right:40px;top:106px;width:250px;height:38px;border:1px solid #ccc;display:flex;align-items:center;justify-content:space-between;padding:0 12px;color:#999;font-size:14px}

/* hero */
.hero{position:relative;height:532px;background:linear-gradient(160deg,#5b4d45 0%,#3a3431 45%,#6d6660 75%,#2f2c2b 100%);color:var(--white);text-align:center}
.hero h1{position:absolute;top:180px;left:0;right:0;font-family:"Oswald",sans-serif;font-weight:700;font-size:50px;letter-spacing:3px;text-shadow:0 2px 6px rgba(0,0,0,.5)}
.hero p{position:absolute;top:250px;left:0;right:0;font-family:"Oswald",sans-serif;font-size:28px;text-shadow:0 2px 6px rgba(0,0,0,.5)}
.hero .btn-outline{position:absolute;top:314px;left:530px;width:140px;height:44px;border:2px solid var(--blue);line-height:40px;font-size:15px;color:var(--white);background:rgba(29,111,191,.25)}
.slider-arrows{position:absolute;right:24px;bottom:20px;display:flex;gap:6px}
.slider-arrows span{width:40px;height:40px;background:rgba(0,0,0,.65);display:flex;align-items:center;justify-content:center}

/* welcome */
.welcome{position:relative;height:328px;padding:56px 40px 0}
.welcome-text{width:680px}
.welcome-text h2{font-family:"Oswald",sans-serif;color:var(--blue);font-size:24px;line-height:1.25;font-weight:500}
.welcome-text p{margin-top:16px;font-size:14px;color:#555;line-height:1.75}
.featured{position:absolute;right:40px;top:56px;width:360px}
.featured h3{font-family:"Oswald",sans-serif;font-size:20px;color:var(--navy);border-bottom:2px solid #ddd;padding-bottom:6px;font-weight:500}
.featured .video{margin-top:12px;height:150px;background:linear-gradient(135deg,#8a7a6a,#c8b9a5 60%,#6f6259);position:relative}
.featured .play{position:absolute;left:150px;top:45px}
.featured p{margin-top:10px;font-size:13px;color:#666}

/* programs */
.programs{position:relative;height:520px;background:var(--light);padding:36px 40px 0}
.section-title{font-family:"Oswald",sans-serif;font-size:28px;color:var(--navy);font-weight:700;letter-spacing:.5px}
.programs .section-title{border-bottom:3px solid var(--blue);display:inline-block;padding-bottom:4px}
.card-arrows{position:absolute;right:40px;top:44px;display:flex;gap:10px;color:#888}
.cards{display:flex;gap:28px;margin-top:24px}
.card{width:259px;background:var(--white);padding-bottom:20px}
.card h4{background:var(--blue);color:var(--white);font-size:15px;font-weight:700;padding:10px 14px;min-height:64px;line-height:1.3}
.card .thumb{height:140px;margin:14px 14px 0}
.card p{margin:14px 14px 0;font-size:13px;color:#666;line-height:1.6}
.read-more{display:inline-block;margin:16px 14px 0;border:2px solid var(--blue);border-radius:20px;padding:4px 16px;font-size:12px;font-weight:700;color:var(--blue)}

/* banner */
.study-banner{position:relative;height:340px;margin-top:40px;background:var(--green);overflow:hidden}
.study-banner .photo{position:absolute;left:0;top:0;width:640px;height:340px;background:linear-gradient(90deg,#c9d9b0 0%,#a8cf6a 70%,var(--green) 100%)}
.study-text{position:absolute;left:680px;top:90px;color:var(--white);font-family:"Oswald",sans-serif}
.study-text .big{font-size:56px;font-weight:700;line-height:1}
.study-text .small{font-size:28px;font-weight:500;margin-top:6px}
.study-text .cta{display:inline-block;margin-top:18px;background:#111;color:var(--white);font-size:24px;font-weight:700;padding:6px 26px}

/* testimonial + form */
.lower{position:relative;height:812px}
.testimony{position:absolute;left:40px;top:40px;width:620px;text-align:center}
.testimony .section-title{font-size:22px}
.quote-badge{width:60px;height:60px;border-radius:50%;background:var(--blue);margin:22px auto 0;display:flex;align-items:center;justify-content:center}
.testimony blockquote{margin-top:24px;font-style:italic;color:#666;font-size:14px;line-height:1.8}
.person{display:flex;align-items:center;justify-content:center;gap:12px;margin-top:22px}
.avatar{width:54px;height:54px;border-radius:50%;background:#b8a898}
.person b{display:block;font-size:14px;text-align:left}
.person small{color:var(--muted);font-size:12px}
.dots{margin-top:14px;display:flex;justify-content:center;gap:6px}
.dots span{width:8px;height:8px;border-radius:50%;background:#ccc}
.dots span:first-child{background:var(--blue)}
.alerts{position:absolute;left:40px;top:500px;width:620px;height:260px;background:var(--light);text-align:center;padding-top:34px}
.alerts h3{font-family:"Oswald",sans-serif;color:var(--blue);font-size:26px;font-weight:700}
.alerts p{margin-top:12px;color:#666;font-size:14px}
.subscribe{display:flex;justify-content:center;margin-top:26px}
.subscribe span{width:340px;height:44px;background:var(--white);border:1px solid #ccc;text-align:left;padding:11px 14px;color:#999}
.subscribe b{width:110px;height:44px;background:var(--blue);color:var(--white);line-height:44px;font-size:14px}
.question{position:absolute;right:40px;top:20px;width:460px;height:740px;background:var(--blue);color:var(--white);padding:30px 28px}
.question h3{font-family:"Oswald",sans-serif;font-size:24px;font-weight:700;border-bottom:1px solid rgba(255,255,255,.4);padding-bottom:12px}
.question label{display:block;font-size:14px;font-weight:700;margin-top:20px}
.row{display:flex;gap:14px}
.field{flex:1;height:42px;background:var(--white);margin-top:8px;color:#999;padding:10px 12px;font-size:13px}
.field.area{height:140px}
.submit{margin-top:34px;height:54px;background:var(--green-btn);text-align:center;line-height:54px;font-family:"Oswald",sans-serif;font-size:24px;font-weight:700}

/* get in touch */
.touch{display:flex;height:88px;background:var(--blue);color:var(--white);font-size:12px}
.touch-title{width:260px;background:var(--blue-dark);font-family:"Oswald",sans-serif;font-size:26px;font-weight:700;display:flex;align-items:center;padding-left:40px}
.touch-item{flex:1;display:flex;align-items:center;gap:10px;padding-left:24px;line-height:1.4}
.touch-item b{display:block;font-size:14px}

/* footer */
.site-footer{height:320px;background:var(--footer);color:#bbb;display:flex;gap:40px;padding:26px 40px 0;font-size:12.5px}
.site-footer h5{font-family:"Oswald",sans-serif;color:var(--white);font-size:16px;font-weight:500;margin-bottom:12px;letter-spacing:.5px}
.site-footer li{list-style:none;line-height:1.9}
.col-nav{width:170px}.col-prog{width:260px}.col-news{width:300px}.col-follow{flex:1}
.news li{line-height:1.4;margin-bottom:10px}
.news li small{display:block;color:var(--muted)}
.follow-row{display:flex;gap:8px;margin-bottom:22px}
.follow-row span{width:30px;height:30px;border-radius:50%;background:#555}
.partner{font-family:"Oswald",sans-serif;color:var(--white);font-size:20px;font-weight:700;line-height:1.2}
.partner-badge{width:120px;height:40px;background:#111;margin-top:10px}
.copyright{height:40px;background:var(--footer-deep);color:#888;text-align:center;line-height:40px;font-size:12px}
</style>
</head>
<body>

<header class="site-header">
  <div class="brand">
    <span class="brand-mark"></span>
    <div>
      <div class="brand-name">CORVALE</div>
      <div class="brand-sub">INSTITUTE OF BUSINESS &amp; TECHNOLOGY</div>
    </div>
  </div>
  <div class="contact-strip">
    <div class="contact-item">
      <svg width="22" height="22" viewBox="0 0 24 24"><path d="M6.6 10.8a15 15 0 0 0 6.6 6.6l2.2-2.2c.3-.3.7-.4 1-.2 1.1.4 2.3.6 3.6.6.6 0 1 .4 1 1V20c0 .6-.4 1-1 1C10.6 21 3 13.4 3 4c0-.6.4-1 1-1h3.5c.6 0 1 .4 1 1 0 1.3.2 2.5.6 3.6.1.3 0 .7-.2 1z" fill="#0f2c52"/></svg>
      <div><small>Call us</small>+260 211 555 014</div>
    </div>
    <div class="contact-item">
      <svg width="22" height="22" viewBox="0 0 24 24"><rect x="2" y="5" width="20" height="14" rx="1" fill="#0f2c52"/><path d="M3 6l9 7 9-7" stroke="#fff" stroke-width="1.5" fill="none"/></svg>
      <div><small>Email us</small>info@corvaleinstitute.com</div>
    </div>
    <div class="socials"><span></span><span></span><span></span><span></span><span></span></div>
  </div>
  <nav class="main-nav">
    <span>HOME</span><span>ABOUT US</span><span>COURSES</span><span>CONTACT US</span>
  </nav>
  <div class="search">Search
    <svg width="16" height="16" viewBox="0 0 24 24"><circle cx="10" cy="10" r="7" stroke="#999" stroke-width="2.5" fill="none"/><path d="M15 15l6 6" stroke="#999" stroke-width="2.5"/></svg>
  </div>
</header>

<section class="hero" role="img" aria-label="Photo of a desk with laptop, keyboard and notebook seen from above">
  <h1>LOREM IPSUM DOLOR SIT AMET</h1>
  <p>Lorem ipsum dolor sit amet, consectetur adipiscing elit, sed do eiusmod tempor.</p>
  <span class="btn-outline">LEARN MORE</span>
  <div class="slider-arrows">
    <span><svg width="12" height="16" viewBox="0 0 12 16"><path d="M9 2L3 8l6 6" stroke="#fff" stroke-width="2.5" fill="none"/></svg></span>
    <span><svg width="12" height="16" viewBox="0 0 12 16"><path d="M3 2l6 6-6 6" stroke="#fff" stroke-width="2.5" fill="none"/></svg></span>
  </div>
</section>

<section class="welcome">
  <div class="welcome-text">
    <h2>WELCOME TO<br>CORVALE INSTITUTE OF BUSINESS AND TECHNOLOGY</h2>
    <p>Corvale Institute of Business and Technology is a fast growing Education &amp; Training Solution Provider, focusing on holistic knowledge and skills interventions that impact livelihoods. It is established on the core values of making a meaningful and measurable difference on career aspirations and growth through innovative learning and knowledge management intervention. We prepare students not only for professional careers but also inculcate the equal sense of discipline and equip them physically, mentally, socially and spiritually. The Institution is licensed and registered under the Westbrook Vocational Skills Council.</p>
  </div>
  <aside class="featured">
    <h3>FEATURED VIDEO</h3>
    <div class="video" role="img" aria-label="Video still of students in a classroom">
      <svg class="play" width="60" height="60" viewBox="0 0 60 60"><circle cx="30" cy="30" r="28" fill="rgba(0,0,0,.55)"/><path d="M24 18l18 12-18 12z" fill="#fff"/></svg>
    </div>
    <p>Lorem ipsum dolor sit amet, consectetur adipiscing elit, sed do eiusmod tempor incididunt.</p>
  </aside>
</section>

<section class="programs">
  <h2 class="section-title">PROGRAMS OFFERED</h2>
  <div class="card-arrows">
    <svg width="14" height="18" viewBox="0 0 12 16"><path d="M9 2L3 8l6 6" stroke="#888" stroke-width="2.5" fill="none"/></svg>
    <svg width="14" height="18" viewBox="0 0 12 16"><path d="M3 2l6 6-6 6" stroke="#888" stroke-width="2.5" fill="none"/></svg>
  </div>
  <div class="cards">
    <article class="card">
      <h4>University Education – Long Distance Learning</h4>
      <div class="thumb" role="img" aria-label="Photo of graduates in caps and gowns" style="background:linear-gradient(135deg,#2c3e58,#6a7d99)"></div>
      <p>Lorem ipsum dolor sit amet, consectetur adipiscing elit, sed do eiusmod tempor incididunt ut labore et dolore magna aliqua.</p>
      <span class="read-more">READ MORE</span>
    </article>
    <article class="card">
      <h4>Modular Soft Skills</h4>
      <div class="thumb" role="img" aria-label="Photo of a business team meeting" style="background:linear-gradient(135deg,#4a6f99,#a9c3de)"></div>
      <p>Lorem ipsum dolor sit amet, consectetur adipiscing elit, sed do eiusmod tempor incididunt ut labore et dolore magna aliqua.</p>
      <span class="read-more">READ MORE</span>
    </article>
    <article class="card">
      <h4>Direct to Device (D2D)</h4>
      <div class="thumb" role="img" aria-label="Illustration of a tablet surrounded by app icons" style="background:linear-gradient(135deg,#3b8bd6,#9fd06a)"></div>
      <p>Lorem ipsum dolor sit amet, consectetur adipiscing elit, sed do eiusmod tempor incididunt ut labore et dolore magna aliqua.</p>
      <span class="read-more">READ MORE</span>
    </article>
    <article class="card">
      <h4>Skillpath</h4>
      <div class="thumb" role="img" aria-label="Photo of a professional in a bright office" style="background:linear-gradient(135deg,#d8dde4,#8b98a8)"></div>
      <p>Lorem ipsum dolor sit amet, consectetur adipiscing elit, sed do eiusmod tempor incididunt ut labore et dolore magna aliqua.</p>
      <span class="read-more">READ MORE</span>
    </article>
  </div>
</section>

<section class="study-banner">
  <div class="photo" role="img" aria-label="Photo of a student lying down working on a laptop"></div>
  <div class="study-text">
    <div class="big">ONLINE STUDY</div>
    <div class="small">RESOURCE WHICH FREE</div>
    <span class="cta">CLICK HERE</span>
  </div>
</section>

<section class="lower">
  <div class="testimony">
    <h2 class="section-title">WHAT OUR PEOPLE SAY</h2>
    <div class="quote-badge"><svg width="26" height="22" viewBox="0 0 26 22"><path d="M0 22V12C0 5 4 1 10 0v4c-3 1-5 3-5 7h5v11zM16 22V12c0-7 4-11 10-12v4c-3 1-5 3-5 7h5v11z" fill="#fff"/></svg></div>
    <blockquote>“Lorem ipsum dolor sit amet, consectetur adipiscing elit, sed do eiusmod tempor incididunt ut labore et dolore magna aliqua. Ut enim ad minim veniam, quis nostrud exercitation ullamco laboris nisi ut aliquip ex ea commodo consequat.”</blockquote>
    <div class="person">
      <div class="avatar" role="img" aria-label="Portrait photo of the reviewer"></div>
      <div><b>Lena Ward</b><small>Lorem ipsum dolor</small></div>
    </div>
    <div class="dots"><span></span><span></span><span></span></div>
  </div>

  <div class="alerts">
    <h3>AUCTION ALERTS!</h3>
    <p>Sign up to receive email alerts about our upcoming auctions</p>
    <div class="subscribe"><span>Enter your email address</span><b>Subscribe</b></div>
  </div>

  <form class="question">
    <h3>DO YOU HAVE A QUESTION?</h3>
    <label>Your Name*</label>
    <div class="row"><div class="field">First Name</div><div class="field">Last Name</div></div>
    <label>Email*</label>
    <div class="field">Your Email Address Here</div>
    <label>Phone</label>
    <div class="field">Phone Number</div>
    <label>Comments*</label>
    <div class="field area"></div>
    <div class="submit">SUBMIT</div>
  </form>
</section>

<section class="touch">
  <div class="touch-title">GET IN TOUCH</div>
  <div class="touch-item">
    <svg width="22" height="22" viewBox="0 0 24 24"><path d="M12 2a7 7 0 0 0-7 7c0 5 7 13 7 13s7-8 7-13a7 7 0 0 0-7-7zm0 9.5A2.5 2.5 0 1 1 12 6.5a2.5 2.5 0 0 1 0 5z" fill="#fff"/></svg>
    <div>48 Birchfield Trade Centre,<br>Unit 7, Harlow Road, Westbrook</div>
  </div>
  <div class="touch-item">
    <svg width="22" height="22" viewBox="0 0 24 24"><path d="M6.6 10.8a15 15 0 0 0 6.6 6.6l2.2-2.2c.3-.3.7-.4 1-.2 1.1.4 2.3.6 3.6.6.6 0 1 .4 1 1V20c0 .6-.4 1-1 1C10.6 21 3 13.4 3 4c0-.6.4-1 1-1h3.5c.6 0 1 .4 1 1 0 1.3.2 2.5.6 3.6.1.3 0 .7-.2 1z" fill="#fff"/></svg>
    <div><b>Call us</b>+260 211 555 014<br>+260 211 555 027</div>
  </div>
  <div class="touch-item">
    <svg width="18" height="24" viewBox="0 0 18 24"><rect x="2" y="1" width="14" height="22" rx="2" fill="#fff"/><rect x="4" y="4" width="10" height="14" fill="#1d6fbf"/></svg>
    <div><b>Mobile</b>+260 966 555 083<br>+260 977 555 091</div>
  </div>
  <div class="touch-item">
    <svg width="22" height="22" viewBox="0 0 24 24"><rect x="2" y="5" width="20" height="14" rx="1" fill="#fff"/><path d="M3 6l9 7 9-7" stroke="#1d6fbf" stroke-width="1.5" fill="none"/></svg>
    <div><b>Email us</b>info@corvaleinstitute.com</div>
  </div>
</section>

<footer class="site-footer">
  <div class="col-nav">
    <h5>NAVIGATION</h5>
    <ul><li>Home</li><li>About Us</li><li>Courses</li><li>Contact Us</li></ul>
  </div>
  <div class="col-prog">
    <h5>PROGRAMS OFFERED</h5>
    <ul><li>University Education – Long Distance Learning</li><li>Modular Soft Skills</li><li>Direct to Device (D2D)</li><li>Skillpath</li><li>Research Methods</li><li>Technology Foundations</li></ul>
  </div>
  <div class="col-news">
    <h5>RECENT NEWS</h5>
    <ul class="news">
      <li><small>January 28, 2015</small>Lorem ipsum dolor sit amet consectetur</li>
      <li><small>January 28, 2015</small>Sed do eiusmod tempor incididunt labore</li>
      <li><small>January 28, 2015</small>Ut enim ad minim veniam quis nostrud</li>
    </ul>
  </div>
  <div class="col-follow">
    <h5>FOLLOW US</h5>
    <div class="follow-row"><span></span><span></span><span></span><span></span></div>
    <div class="partner">IN CONJUNCTION<br>WITH SKILLPATH</div>
    <div class="partner-badge"></div>
  </div>
</footer>
<div class="copyright">© 2015 Corvale Institute of Business and Technology. All Rights Reserved.</div>

</body>
</html>
```